Facial Tissue Brand Logo and Design

We would like you to design a Logo for the Facial Tissue Brand "Velora" along with the box design. The pack should indicate the pack size (150 x 2 ply). Also our company logo should be present (attached) along with a barcode. The box size dimensions should be 210mm (L) x 110mm (W) x 70mm (H). We are open to all kinds of nice designs which are attractive but not overdone. Happy designing!

UPDATE:
We appreciate the designs so far... but would also love to see more options in a simple and elegent design style that would look good on a table... please see attached below links for reference purpose:

www.pictovault-example.com/image-photo/cleaning-wipes-isolated-on-white-257770819

www.pictovault-example.com/image-photo/cleaning-wipes-isolated-on-white-155326937

www.pictovault-example.com/image-photo/delicate-female-hands-pulling-tissue-out-1330426586

Happy desgining!

We appreciate the designs so far.. but would like to to see some more options.

```html
<!DOCTYPE html>
<html lang="en">
<head>
<meta charset="utf-8">
<title>Velora Facial Tissue – Box Dieline</title>
<link href="https://fonts.googleapis.com/css2?family=Montserrat:wght@500;600;700&display=swap" rel="stylesheet">
<style>
  :root {
    --navy: #15426f;
    --navy-deep: #0f2d55;
    --blue-mid: #3f6fa6;
    --lavender: #d9dbe7;
    --cream: #ecebd6;
    --copper: #c49576;
    --white: #ffffff;
    --page: #ffffff;
  }
  html, body {
    margin: 0;
    width: 1200px;
    height: 671px;
    overflow: hidden;
    background: var(--page);
    font-family: "Montserrat", sans-serif;
  }
  .dieline {
    position: absolute;
    left: 310px;
    top: 20px;
    width: 580px;
    height: 630px;
    filter: drop-shadow(6px 6px 6px rgba(0,0,0,0.35));
  }
  .flap { fill: var(--navy); }
  .fold { fill: none; stroke: var(--white); stroke-width: 1.4; stroke-dasharray: 4 3; opacity: .7; }
  .window-panel { fill: var(--white); opacity: .5; }
  .brand { font-family: "Montserrat", sans-serif; font-weight: 700; fill: var(--navy); }
  .label { font-family: "Montserrat", sans-serif; font-weight: 600; fill: var(--navy); letter-spacing: 1.5px; }
  .pill-text { font-family: "Montserrat", sans-serif; font-weight: 500; fill: var(--white); }
  .count { font-family: "Montserrat", sans-serif; font-weight: 500; fill: var(--navy); }
  .code-label { font-family: "Montserrat", sans-serif; font-weight: 500; fill: var(--white); }
</style>
</head>
<body>
<svg class="dieline" viewBox="1028 77 870 945" xmlns="http://www.w3.org/2000/svg">
  <defs>
    <linearGradient id="pale-pattern" x1="0" y1="0" x2="1" y2="1">
      <stop offset="0" stop-color="#e9e4d8"/>
      <stop offset=".2" stop-color="#d7d9e6"/>
      <stop offset=".45" stop-color="#cfd2e1"/>
      <stop offset=".7" stop-color="#e2d3c6"/>
      <stop offset=".85" stop-color="#d3d6e4"/>
      <stop offset="1" stop-color="#b9c6dc"/>
    </linearGradient>
    <linearGradient id="navy-pattern" x1="0" y1="1" x2="1" y2="0">
      <stop offset="0" stop-color="#dfe0cd"/>
      <stop offset=".22" stop-color="#a9bccf"/>
      <stop offset=".38" stop-color="#b88a6a"/>
      <stop offset=".52" stop-color="#2d5a90"/>
      <stop offset=".75" stop-color="#193c6c"/>
      <stop offset="1" stop-color="#0f2d55"/>
    </linearGradient>
  </defs>

  <!-- tuck flap -->
  <polygon class="flap" points="1215,77 1700,77 1722,130 1200,130"/>

  <!-- side flaps -->
  <g class="side-flaps">
    <rect class="flap" x="1030" y="145" width="185" height="245" rx="30"/>
    <rect class="flap" x="1708" y="145" width="190" height="245" rx="30"/>
    <polygon class="flap" points="1030,425 1200,400 1200,570 1030,555"/>
    <polygon class="flap" points="1722,400 1898,425 1898,555 1722,570"/>
    <rect class="flap" x="1030" y="592" width="185" height="246" rx="30"/>
    <rect class="flap" x="1708" y="592" width="190" height="246" rx="30"/>
    <polygon class="flap" points="1030,872 1200,850 1200,1022 1030,1022"/>
    <polygon class="flap" points="1722,850 1898,872 1898,1022 1722,1022"/>
  </g>

  <!-- base panel (printed upside down) -->
  <g class="panel panel-base">
    <rect x="1200" y="130" width="522" height="270" fill="url(#pale-pattern)" role="img" aria-label="Soft lavender geometric pattern with copper arcs"/>
    <rect class="window-panel" x="1210" y="138" width="505" height="252" rx="16"/>
    <g class="code-box">
      <rect x="1590" y="152" width="113" height="57" fill="var(--navy)"/>
      <text class="code-label" x="1646" y="176" font-size="11" text-anchor="middle" transform="rotate(180 1646 180)">bar code</text>
    </g>
    <g transform="rotate(180 1470 260)">
      <text class="label" x="1470" y="313" font-size="22" text-anchor="middle">FACIAL TISSUE</text>
      <rect x="1424" y="236" width="16" height="16" fill="var(--navy)"/>
      <text class="brand" x="1448" y="253" font-size="28">Velora</text>
    </g>
  </g>

  <!-- back side panel -->
  <g class="panel panel-side">
    <rect x="1200" y="400" width="522" height="170" fill="url(#pale-pattern)" role="img" aria-label="Soft lavender geometric pattern with copper arcs"/>
    <rect class="window-panel" x="1210" y="410" width="505" height="155" rx="16"/>
    <rect x="1412" y="470" width="14" height="14" fill="var(--navy)"/>
    <text class="brand" x="1433" y="484" font-size="23">Velora</text>
    <text class="label" x="1470" y="533" font-size="16" text-anchor="middle">FACIAL TISSUE</text>
  </g>

  <!-- top panel with dispenser opening -->
  <g class="panel panel-top">
    <rect x="1200" y="570" width="522" height="280" fill="url(#navy-pattern)" role="img" aria-label="Navy fan and hexagon pattern with cream lattice, copper arcs and torn blue shapes"/>
    <rect x="1302" y="640" width="323" height="145" rx="18" fill="var(--white)"/>
    <rect x="1412" y="680" width="16" height="16" fill="var(--navy)"/>
    <text class="brand" x="1436" y="697" font-size="30">Velora</text>
    <text class="label" x="1470" y="767" font-size="20" text-anchor="middle">FACIAL TISSUE</text>
    <text class="count" x="1228" y="830" font-size="24">150 x 2 ply</text>
  </g>

  <!-- front side panel -->
  <g class="panel panel-front">
    <rect x="1200" y="850" width="522" height="172" fill="url(#pale-pattern)" role="img" aria-label="Soft lavender geometric pattern with copper arcs"/>
    <rect class="window-panel" x="1210" y="858" width="505" height="157" rx="16"/>
    <rect x="1284" y="916" width="16" height="16" fill="var(--navy)"/>
    <text class="brand" x="1307" y="933" font-size="28">Velora</text>
    <text class="label" x="1337" y="990" font-size="19" text-anchor="middle">FACIAL TISSUE</text>
    <path d="M1520,967 H1722 V994 H1520 A13.5,13.5 0 0 1 1520,967 Z" fill="var(--navy)"/>
    <text class="pill-text" x="1518" y="986" font-size="14">ULTRA SOFT&#160;&#160;&#160;150 x 2 ply</text>
  </g>

  <!-- fold lines -->
  <g class="folds">
    <line class="fold" x1="1200" y1="130" x2="1200" y2="1022"/>
    <line class="fold" x1="1722" y1="130" x2="1722" y2="1022"/>
    <line class="fold" x1="1200" y1="130" x2="1722" y2="130"/>
    <line class="fold" x1="1200" y1="400" x2="1722" y2="400"/>
    <line class="fold" x1="1200" y1="570" x2="1722" y2="570"/>
    <line class="fold" x1="1200" y1="850" x2="1722" y2="850"/>
  </g>
</svg>
</body>
</html>
```